Counseling Practice Business Card

I need a professional looking business card incorporating my new logo that was just completed. Card needs to incorporate my name and title, description of my specialty, my address, my phone number, my fax number, my email and my website URL. I need to be able to choose design on/with different paper colors and textures.
I do not have a lot of business card ideas so I am open to anything but I want bold,sharp, clear card without additional designs other than my logo (see attached file info). I am open to different color backgrounds or paper colors including black. I do not like traditional brackets around area codes in phone number or dashes between numbers in phone number. Am open to other ways of presenting including periods between numbers as appropriate. I do not know enough to know what I like yet but I want card to coordinate and work together with my logo. My practice emphasizes natural mental health interventions so any use of color (with background paper color or the blue and green in my logo) that elicits nature is nice. In addition to black, any natural brown or wood looking background might be desirable also. Most of the offerings so far look very similar and boring.

Target Market(s)

Potential therapy clients and other professionals

Contact Information for Business Card

Card information:
Gerald M. Whitcombe, Ph.D.
Licensed Clinical Psychologist
Integrative Health Coach
4812 Marlowe Ridge Blvd SE
Suite 310
Alderbrook, GA 30287
(770) 415-2983 phone
(770) 581-4096 fax
drgeraldwhitcombe@quillmarsh.net
brightfernwellness.net

Font styles to use
Serif
Sans Serif
Other font styles liked:
• anything that you think looks crisp, clear and easily readable

Requirements
Must have
• Any color used should coordinate with my logo design (see attached files).
• Card should be printed horizontally so top and bottom are longest sides of rectangle.
• Background color or paper color should complement and highlight logo. Do not like a white background. black, grey, brown or any color my logo would blend well with.
Nice to have
• I would like designer to utilize color to highlight letters/name or phone-fax-web symbols.
• Bottom edge of card could be highlighted if appropriate to an idea.
Should not have
• I would NOT want the card to have a pure white background at all.
• No clear cards.
• Cards should be oriented with long sides on bottom and top, NOT sides. DO NOT LIKE THIS THIN TALL ORIENTATION.

```html
<!DOCTYPE html>
<html lang="en">
<head>
<meta charset="utf-8">
<title>Brightfern Wellness – Business Card</title>
<link rel="stylesheet" href="https://fonts.googleapis.com/css2?family=Roboto:wght@400;500&family=Roboto+Condensed:wght@400;700&display=swap">
<style>
  :root {
    --backdrop: #e8e5e0;
    --card-dark: #131518;
    --brand-blue: #2a73b5;
    --brand-green: #0f6b34;
    --text-light: #ffffff;
    --url-grey: #b9bcc0;
    --shadow: rgba(0, 0, 0, 0.35);
  }
  * { margin: 0; padding: 0; box-sizing: border-box; }
  html, body {
    width: 1200px; height: 960px; overflow: hidden;
    background: var(--backdrop);
  }
  .canvas { position: relative; width: 1200px; height: 960px; }

  .card {
    position: absolute; width: 601px; height: 342px;
    overflow: hidden; box-shadow: 0 3px 10px var(--shadow);
  }
  .card--front { left: 314px; top: 113px; background: var(--brand-blue); }
  .card--back  { left: 311px; top: 472px; background: var(--card-dark); }

  .card__shape { position: absolute; inset: 0; }

  .contact-block {
    position: absolute; left: 34px; top: 42px;
    color: var(--text-light);
    font-family: "Roboto", sans-serif;
  }
  .contact-block__name {
    font-family: "Roboto Condensed", sans-serif;
    font-weight: 700; font-size: 18px; letter-spacing: 0.2px;
    text-transform: uppercase; line-height: 24px;
  }
  .contact-block__role {
    font-family: "Roboto Condensed", sans-serif;
    font-size: 14.5px; line-height: 19px;
  }
  .contact-block__address {
    margin-top: 61px; font-size: 14px; line-height: 18px; font-style: normal;
  }
  .contact-list { list-style: none; margin-top: 10px; }
  .contact-list li {
    display: flex; align-items: center; gap: 8px;
    font-size: 13.5px; line-height: 19px; height: 19px;
  }
  .contact-list .email { font-size: 12.5px; }
  .contact-list svg { width: 13px; height: 13px; flex: none; fill: var(--text-light); }

  .brand-name {
    position: absolute; text-align: center;
    font-family: "Roboto", sans-serif; font-weight: 500;
    color: var(--brand-blue);
  }
  .brand-name__main { display: block; line-height: 1; }
  .brand-name__sub {
    display: block; text-transform: uppercase; line-height: 1;
  }
  .card--front .brand-name { left: 330px; top: 140px; width: 216px; }
  .card--front .brand-name__main { font-size: 40px; }
  .card--front .brand-name__sub { font-size: 15px; letter-spacing: 4.6px; margin-top: 4px; }

  .card--back .brand-name { left: 150px; top: 116px; width: 300px; }
  .card--back .brand-name__main { font-size: 56px; }
  .card--back .brand-name__sub { font-size: 20px; letter-spacing: 6.6px; margin-top: 6px; }

  .card__url {
    position: absolute; left: 0; right: 0; top: 284px; text-align: center;
    font-family: "Roboto", sans-serif; font-size: 14px; letter-spacing: 3.6px;
    color: var(--url-grey);
  }
</style>
</head>
<body>
<main class="canvas">

  <section class="card card--front">
    <svg class="card__shape" viewBox="0 0 601 342" aria-hidden="true">
      <ellipse cx="480" cy="175" rx="227" ry="217" fill="var(--card-dark)"/>
      <ellipse cx="480" cy="175" rx="226" ry="216" fill="var(--brand-green)"/>
      <ellipse cx="491" cy="175" rx="222" ry="212" fill="var(--card-dark)"/>
    </svg>

    <div class="contact-block">
      <h1 class="contact-block__name">Gerald M. Whitcombe, Ph.D.</h1>
      <p class="contact-block__role">Licensed Clinical Psychologist</p>
      <p class="contact-block__role">Integrative Health Coach</p>

      <address class="contact-block__address">
        4812 Marlowe Ridge Blvd SE<br>
        Suite 310<br>
        Alderbrook, GA 30287
      </address>

      <ul class="contact-list">
        <li>
          <svg viewBox="0 0 16 16" aria-label="Phone"><path d="M3.6 1.2l2.3 2.6-1.3 2a9 9 0 0 0 5.6 5.6l2-1.3 2.6 2.3-1.4 2.4C8.2 15 1 7.8 1.2 2.6z"/></svg>
          <span>(770) 415-2983</span>
        </li>
        <li>
          <svg viewBox="0 0 16 16" aria-label="Fax"><path d="M4 1h8v4H4zM1 6h14v6h-2v-2H3v2H1zM4 11h8v4H4z"/></svg>
          <span>(770) 581-4096</span>
        </li>
        <li>
          <svg viewBox="0 0 16 16" aria-label="Email"><path d="M1 3h14v1.4L8 9 1 4.4zM1 6l7 4.6L15 6v7H1z"/></svg>
          <span class="email">drgeraldwhitcombe@quillmarsh.net</span>
        </li>
        <li>
          <svg viewBox="0 0 16 16" aria-label="Website"><path d="M8 1a7 7 0 1 0 0 14A7 7 0 0 0 8 1zm-1 2.2c-1 .6-1.6 1.6-1 2.6s2 .4 2.4 1.6-1 1.8-.4 3 1.6 1 1.6 2.4a5 5 0 0 1-6-6.4c.8.2 1.4.8 2 .4S5.6 3.6 7 3.2zm3.4.4a5 5 0 0 1 2.4 5.6c-.6-.4-1.2-1.6-2-1.2s-1-1.2-.4-2 .6-1.6 0-2.4z"/></svg>
          <span>www.brightfernwellness.net</span>
        </li>
      </ul>
    </div>

    <p class="brand-name">
      <span class="brand-name__main">Brightfern</span>
      <span class="brand-name__sub">Wellness</span>
    </p>
  </section>

  <section class="card card--back">
    <p class="brand-name">
      <span class="brand-name__main">Brightfern</span>
      <span class="brand-name__sub">Wellness</span>
    </p>
    <p class="card__url">www.brightfernwellness.net</p>
  </section>

</main>
</body>
</html>
```